Car wash line needed for the pylon inscription

We need a design template / print template for our advertising pylon so that the Korvane plates can be printed. The area to be printed is approx. 1.5m wide and approx. 2.70m high. We operate a car wash about 30m long. The washing rollers are equipped with scratch-free Velmo Tex foam material. Before the vehicle is put into the car wash it gets a manual high pressure pre-wash. There are four different washing programs: basic laundry € 7.50 (wheel cleaning, intensive washing, gloss drying comfort care € 10.50 (like base + active foam) special care € 13.00 (like comfort + glossy sealing with lotus wax) premium care € 15.50 (like special care + Underbody wash) The pylon is right on the driveway on a busy road, we want to achieve maximum attention with the pylons. It should not be too much content because the vehicles drive past it, due to an immediate gyro, the speed is however at about 40Km / h. Opening hours Mon-Fri. 08: 00-19: 00 Sat 07: 00-19: 00 The Korvane plates are red. The enclosed files show our pylon with a little appealing design proposal our advertising agency and the real local places. For the opinion you can see on the following link a youtube video with a comparable car wash like ours, the washing process is well illustrated there. https://www.clipvault-demo.net/watch?v=Qk7rTzP2mLw Furthermore, we have a bonus card system who has washed our car 10 times gets the 11 laundry for free. From foam additives we use active foam from the comfort care and from the special care gets the vehicle lotus wax, which has the effect that the paint is sealed and keeps the shine longer. We need a design template / print template for our advertising pylon so that the Korvane plates can be printed. The area to be printed is approx. 1.5m wide and approx. 2.70m high. We operate a car wash about 30m long. The washing rollers are equipped with scratch-free Velmo Tex foam material. Before the vehicle is put into the car wash it gets a manual high pressure pre-wash. There are four different washing programs: basic laundry € 7.50 (wheel cleaning, intensive washing, gloss drying comfort care € 10.50 (like base + active foam) special care € 13.00 (like comfort + glossy sealing with lotus wax) premium care € 15.50 (like special care + Underbody wash) The pylon is right on the driveway on a busy road, we want to achieve maximum attention with the pylons. It should not be too much content because the vehicles drive past it, due to an immediate gyro, the speed is however at about 40Km / h. Opening hours Mon-Fri. 08: 00-19: 00 Sat 07: 00-19: 00 The Korvane plates are red. The enclosed files show our pylon with a little appealing design proposal our advertising agency and the real local places. For the opinion you can see on the following link a youtube video with a comparable car wash like ours, the washing process is well illustrated there. https://www.clipvault-demo.net/watch?v=Qk7rTzP2mLw Furthermore, we have a bonus card system who has washed our car 10 times gets the 11 laundry for free. From foam additives we use active foam from the comfort care and from the special care gets the vehicle lotus wax, which has the effect that the paint is sealed and keeps the shine longer. We need a design template / print template for our advertising pylon so that the Korvane plates can be printed. The area to be printed is approx. 1.5m wide and approx. 2.70m high. We operate a car wash about 30m long. The washing rollers are equipped with scratch-free Velmo Tex foam material. Before the vehicle is put into the car wash it gets a manual high pressure pre-wash. There are four different washing programs: basic laundry € 7.50 (wheel cleaning, intensive washing, gloss drying comfort care € 10.50 (like base + active foam) special care € 13.00 (like comfort + glossy sealing with lotus wax) premium care € 15.50 (like special care + Underbody wash) The pylon is right on the driveway on a busy road, we want to achieve maximum attention with the pylons. It should not be too much content because the vehicles drive past it, due to an immediate gyro, the speed is however at about 40Km / h. Opening hours Mon-Fri. 08: 00-19: 00 Sat 07: 00-19: 00 The Korvane plates are red. The enclosed files show our pylon with a little appealing design proposal our advertising agency and the real local places. For the opinion you can see on the following link a youtube video with a comparable car wash like ours, the washing process is well illustrated there. https://www.clipvault-demo.net/watch?v=Qk7rTzP2mLw Furthermore, we have a bonus card system who has washed our car 10 times gets the 11 laundry for free. From foam additives we use active foam from the comfort care and from the special care gets the vehicle lotus wax, which has the effect that the paint is sealed and keeps the shine longer. We need a design template / print template for our advertising pylon so that the Korvane plates can be printed. The area to be printed is approx. 1.5m wide and approx. 2.70m high. We operate a car wash about 30m long. The washing rollers are equipped with scratch-free Velmo Tex foam material. Before the vehicle is put into the car wash it gets a manual high pressure pre-wash. There are four different washing programs: basic laundry € 7.50 (wheel cleaning, intensive washing, gloss drying comfort care € 10.50 (like base + active foam) special care € 13.00 (like comfort + glossy sealing with lotus wax) premium care € 15.50 (like special care + Underbody wash) The pylon is right on the driveway on a busy road, we want to achieve maximum attention with the pylons. It should not be too much content because the vehicles drive past it, due to an immediate gyro, the speed is however at about 40Km / h. Opening hours Mon-Fri. 08: 00-19: 00 Sat 07: 00-19: 00 The Korvane plates are red. The enclosed files show our pylon with a little appealing design proposal our advertising agency and the real local places. For the opinion you can see on the following link a youtube video with a comparable car wash like ours, the washing process is well illustrated there. https://www.clipvault-demo.net/watch?v=Qk7rTzP2mLw Furthermore, we have a bonus card system who has washed our car 10 times gets the 11 laundry for free. From foam additives we use active foam from the comfort care and from the special care gets the vehicle lotus wax, which has the effect that the paint is sealed and keeps the shine longer. We need a design template / print template for our advertising pylon so that the Korvane plates can be printed. The area to be printed is approx. 1.5m wide and approx. 2.70m high. We operate a car wash about 30m long. The washing rollers are equipped with scratch-free Velmo Tex foam material. Before the vehicle is put into the car wash it gets a manual high pressure pre-wash. There are four different washing programs: basic laundry € 7.50 (wheel cleaning, intensive washing, gloss drying comfort care € 10.50 (like base + active foam) special care € 13.00 (like comfort + glossy sealing with lotus wax) premium care € 15.50 (like special care + Underbody wash) The pylon is right on the driveway on a busy road, we want to achieve maximum attention with the pylons. It should not be too much content because the vehicles drive past it, due to an immediate gyro, the speed is however at about 40Km / h. Opening hours Mon-Fri. 08: 00-19: 00 Sat 07: 00-19: 00 The Korvane plates are red. The enclosed files show our pylon with a little appealing design proposal our advertising agency and the real local places. For the opinion you can see on the following link a youtube video with a comparable car wash like ours, the washing process is well illustrated there. https://www.clipvault-demo.net/watch?v=Qk7rTzP2mLw Furthermore, we have a bonus card system who has washed our car 10 times gets the 11 laundry for free. From foam additives we use active foam from the comfort care and from the special care gets the vehicle lotus wax, which has the effect that the paint is sealed and keeps the shine longer. We need a design template / print template for our advertising pylon so that the Korvane plates can be printed. The area to be printed is approx. 1.5m wide and approx. 2.70m high. We operate a car wash about 30m long. The washing rollers are equipped with scratch-free Velmo Tex foam material. Before the vehicle is put into the car wash it gets a manual high pressure pre-wash. There are four different washing programs: basic laundry € 7.50 (wheel cleaning, intensive washing, gloss drying comfort care € 10.50 (like base + active foam) special care € 13.00 (like comfort + glossy sealing with lotus wax) premium care € 15.50 (like special care + Underbody wash) The pylon is right on the driveway on a busy road, we want to achieve maximum attention with the pylons. It should not be too much content because the vehicles drive past it, due to an immediate gyro, the speed is however at about 40Km / h. Opening hours Mon-Fri. 08: 00-19: 00 Sat 07: 00-19: 00 The Korvane plates are red. The enclosed files show our pylon with a little appealing design proposal our advertising agency and the real local places. For the opinion you can see on the following link a youtube video with a comparable car wash like ours, the washing process is well illustrated there. https://www.clipvault-demo.net/watch?v=Qk7rTzP2mLw Furthermore, we have a bonus card system who has washed our car 10 times gets the 11 laundry for free. From foam additives we use active foam from the comfort care and from the special care gets the vehicle lotus wax, which has the effect that the paint is sealed and keeps the shine longer. We need a design template / print template for our advertising pylon so that the Korvane plates can be printed. The area to be printed is approx. 1.5m wide and approx. 2.70m high. We operate a car wash about 30m long. The washing rollers are equipped with scratch-free Velmo Tex foam material. Before the vehicle is put into the car wash it gets a manual high pressure pre-wash. There are four different washing programs: basic laundry € 7.50 (wheel cleaning, intensive washing, gloss drying comfort care € 10.50 (like base + active foam) special care € 13.00 (like comfort + glossy sealing with lotus wax) premium care € 15.50 (like special care + Underbody wash) The pylon is right on the driveway on a busy road, we want to achieve maximum attention with the pylons. It should not be too much content because the vehicles drive past it, due to an immediate gyro, the speed is however at about 40Km / h. Opening hours Mon-Fri. 08: 00-19: 00 Sat 07: 00-19: 00 The Korvane plates are red. The enclosed files show our pylon with a little appealing design proposal our advertising agency and the real local places. For the opinion you can see on the following link a youtube video with a comparable car wash like ours, the washing process is well illustrated there. https://www.clipvault-demo.net/watch?v=Qk7rTzP2mLw Furthermore, we have a bonus card system who has washed our car 10 times gets the 11 laundry for free. From foam additives we use active foam from the comfort care and from the special care gets the vehicle lotus wax, which has the effect that the paint is sealed and keeps the shine longer. We need a design template / print template for our advertising pylon so that the Korvane plates can be printed. The area to be printed is approx. 1.5m wide and approx. 2.70m high. We operate a car wash about 30m long. The washing rollers are equipped with scratch-free Velmo Tex foam material. Before the vehicle is put into the car wash it gets a manual high pressure pre-wash. There are four different washing programs: basic laundry € 7.50 (wheel cleaning, intensive washing, gloss drying comfort care € 10.50 (like base + active foam) special care € 13.00 (like comfort + glossy sealing with lotus wax) premium care € 15.50 (like special care + Underbody wash) The pylon is right on the driveway on a busy road, we want to achieve maximum attention with the pylons. It should not be too much content because the vehicles drive past it, due to an immediate gyro, the speed is however at about 40Km / h. Opening hours Mon-Fri. 08: 00-19: 00 Sat 07: 00-19: 00 The Korvane plates are red. The enclosed files show our pylon with a little appealing design proposal our advertising agency and the real local places. For the opinion you can see on the following link a youtube video with a comparable car wash like ours, the washing process is well illustrated there. https://www.clipvault-demo.net/watch?v=Qk7rTzP2mLw Furthermore, we have a bonus card system who has washed our car 10 times gets the 11 laundry for free. From foam additives we use active foam from the comfort care and from the special care gets the vehicle lotus wax, which has the effect that the paint is sealed and keeps the shine longer. We need a design template / print template for our advertising pylon so that the Korvane plates can be printed. The area to be printed is approx. 1.5m wide and approx. 2.70m high. We operate a car wash about 30m long. The washing rollers are equipped with scratch-free Velmo Tex foam material. Before the vehicle is put into the car wash it gets a manual high pressure pre-wash. There are four different washing programs: basic laundry € 7.50 (wheel cleaning, intensive washing, gloss drying comfort care € 10.50 (like base + active foam) special care € 13.00 (like comfort + glossy sealing with lotus wax) premium care € 15.50 (like special care + Underbody wash) The pylon is right on the driveway on a busy road, we want to achieve maximum attention with the pylons. It should not be too much content because the vehicles drive past it, due to an immediate gyro, the speed is however at about 40Km / h. Opening hours Mon-Fri. 08: 00-19: 00 Sat 07: 00-19: 00 The Korvane plates are red. The enclosed files show our pylon with a little appealing design proposal our advertising agency and the real local places. For the opinion you can see on the following link a youtube video with a comparable car wash like ours, the washing process is well illustrated there. https://www.clipvault-demo.net/watch?v=Qk7rTzP2mLw Furthermore, we have a bonus card system who has washed our car 10 times gets the 11 laundry for free. From foam additives we use active foam from the comfort care and from the special care gets the vehicle lotus wax, which has the effect that the paint is sealed and keeps the shine longer.

Target Market(s)

germany

Colors

Designer to choose colors to be used in the design.

Requirements
Must have
• Print template for the print job in the accepted formats. Of course, the design must be in German
Nice to have
• Colors that attract attention, but are still serious. The content must be perceived when passing by and the customers must be aware of the car wash.
Should not have
• Kitschiges Design Too much content which takes longer to be read.

```html
<!DOCTYPE html>
<html lang="de">
<head>
<meta charset="utf-8">
<title>Waschpark am Lindenhof – Pylon</title>
<link rel="stylesheet" href="https://fonts.googleapis.com/css2?family=Anton&family=Archivo+Black&family=Oswald:wght@700&display=swap">
<style>
  :root{
    --red:#c32b32;
    --grey:#727377;
    --grey-edge:#e4e4e6;
    --post:#32343d;
    --navy:#0d2462;
    --blue:#00a3e4;
    --yellow:#ffe500;
    --orange:#f7a11a;
    --tag-green:#0c8a3d;
    --tag-red:#e0202b;
    --tag-purple:#941c68;
    --tag-blue:#1a4aa0;
    --white:#ffffff;
    --ink:#1a1a1a;
  }
  html,body{margin:0;padding:0;overflow:hidden;background:var(--white);}
  .canvas{position:relative;width:780px;height:1200px;overflow:hidden;background:var(--white);}
  .abs{position:absolute;}
  .sign-head{left:0;top:0;width:780px;height:520px;}
  .brand{left:192px;top:318px;width:417px;text-align:center;color:var(--white);font-family:"Anton",sans-serif;text-transform:uppercase;line-height:1;}
  .brand-line1{font-size:58px;letter-spacing:0;}
  .brand-line2{font-size:28px;letter-spacing:2px;margin-top:8px;}
  .post{left:231px;top:483px;width:344px;height:573px;background:var(--post);}
  .leg{top:1056px;width:37px;height:48px;background:var(--post);}
  .leg-left{left:275px;}
  .leg-right{left:484px;}
  .board{left:252px;top:497px;width:299px;height:542px;background:var(--navy);overflow:hidden;}
  .board-header{left:0;top:0;width:299px;height:106px;}
  .claim{left:0;top:12px;width:299px;text-align:center;color:var(--white);font-family:"Archivo Black",sans-serif;text-transform:uppercase;line-height:1.05;}
  .claim-small{font-size:12px;padding-left:20px;}
  .claim-big{font-size:20px;padding-left:20px;}
  .program{left:0;width:299px;height:31px;}
  .program-name{left:0;top:0;width:207px;height:31px;background:var(--yellow);clip-path:polygon(0 0,100% 0,94% 100%,0 100%);color:var(--tag-red);font-family:"Oswald",sans-serif;font-weight:700;font-size:22px;line-height:31px;padding-left:7px;box-sizing:border-box;text-transform:uppercase;}
  .program-price{left:200px;top:0;width:99px;height:31px;clip-path:polygon(12% 0,100% 0,100% 100%,0 100%);color:var(--white);font-family:"Oswald",sans-serif;font-weight:700;font-size:25px;line-height:31px;text-align:right;padding-right:6px;box-sizing:border-box;}
  .price-green{background:var(--tag-green);}
  .price-red{background:var(--tag-red);}
  .price-purple{background:var(--tag-purple);}
  .price-blue{background:var(--tag-blue);}
  .features{left:13px;width:285px;color:var(--white);font-family:"Archivo Black",sans-serif;font-size:10.6px;line-height:14px;text-transform:uppercase;}
  .hours{left:0;top:496px;width:299px;height:46px;}
  .hours-text{left:0;top:506px;width:299px;text-align:center;color:var(--ink);font-family:"Oswald",sans-serif;font-weight:700;text-transform:uppercase;line-height:1.1;}
  .hours-title{font-size:9px;}
  .hours-times{font-size:13.5px;}
</style>
</head>
<body>
<div class="canvas">

  <svg class="abs sign-head" viewBox="0 0 780 520" aria-hidden="true">
    <circle cx="401" cy="240" r="182" fill="var(--grey-edge)"/>
    <circle cx="401" cy="240" r="178" fill="var(--red)"/>
    <path d="M190 311 H615 a25 25 0 0 1 25 25 V458 a25 25 0 0 1 -25 25 H192 V515 L117 462 L192 408 Z" fill="var(--red)"/>
    <circle cx="401" cy="240" r="146" fill="var(--grey-edge)"/>
    <circle cx="401" cy="240" r="143" fill="var(--grey)"/>
    <rect x="190" y="303" width="421" height="149" rx="12" fill="var(--grey-edge)"/>
    <rect x="193" y="306" width="415" height="143" rx="10" fill="var(--grey)"/>
    <rect x="260" y="270" width="281" height="40" fill="var(--grey)"/>
  </svg>

  <div class="abs brand">
    <div class="brand-line1">Waschpark</div>
    <div class="brand-line2">am Lindenhof</div>
  </div>

  <div class="abs post"></div>
  <div class="abs leg leg-left"></div>
  <div class="abs leg leg-right"></div>

  <div class="abs board">
    <svg class="abs board-header" viewBox="0 0 299 106" aria-hidden="true">
      <defs>
        <linearGradient id="headerSky" x1="0" y1="0" x2="1" y2="0">
          <stop offset="0" stop-color="var(--navy)"/>
          <stop offset="0.55" stop-color="#0a4fa8"/>
          <stop offset="1" stop-color="var(--blue)"/>
        </linearGradient>
      </defs>
      <rect width="299" height="106" fill="url(#headerSky)"/>
      <path d="M0 46 C60 80 170 95 299 88 V106 H0 Z" fill="var(--navy)"/>
      <path d="M0 44 C60 78 170 92 299 85 V94 C170 102 60 90 0 54 Z" fill="var(--orange)"/>
      <path d="M0 44 C60 76 170 89 299 82 V87 C170 95 60 82 0 50 Z" fill="var(--yellow)"/>
    </svg>
    <div class="abs claim">
      <div class="claim-small">Lackschonend dank</div>
      <div class="claim-big">Velmo Tex</div>
      <div class="claim-big">Schaumwalzen</div>
    </div>

    <div class="abs program" style="top:115px">
      <div class="abs program-name">Basis Wäsche</div>
      <div class="abs program-price price-green">€ 7,50</div>
    </div>
    <div class="abs features" style="top:155px">HD-Vorwäsche, Felgenreinigung,<br>Intensivwäsche, Glanztrocknung</div>

    <div class="abs program" style="top:191px">
      <div class="abs program-name">Komfortpflege</div>
      <div class="abs program-price price-red">€ 10,50</div>
    </div>
    <div class="abs features" style="top:229px">HD-Vorwäsche, Aktivschaum,<br>Felgenreinigung, Intensivwäsche,<br>Glanztrocknung</div>

    <div class="abs program" style="top:276px">
      <div class="abs program-name">Spezialpflege</div>
      <div class="abs program-price price-purple">€ 13,00</div>
    </div>
    <div class="abs features" style="top:315px">HD-Vorwäsche, Aktivschaum,<br>Felgenreinigung, Intensivwäsche,<br>Glanztrocknung,<br>Hochglanzversieglung mit<br>Lotuswachs</div>

    <div class="abs program" style="top:391px">
      <div class="abs program-name">Premiumpflege</div>
      <div class="abs program-price price-blue">€ 15,50</div>
    </div>
    <div class="abs features" style="top:430px">HD-Vorwäsche, Aktivschaum,<br>Felgenreinigung, Unterbodenwäsche,<br>Intensivwäsche, Glanztrocknung,<br>Hochglanzversieglung<br>mit Lotuswachs</div>

    <svg class="abs hours" viewBox="0 0 299 46" aria-hidden="true">
      <path d="M0 8 C100 0 200 0 299 0 V46 H0 Z" fill="var(--yellow)"/>
    </svg>
    <div class="abs hours-text">
      <div class="hours-title">Öffnungszeiten</div>
      <div class="hours-times">Mo-Fr. : 08:00-19:00 / Sa. : 07:00-19:00</div>
    </div>
  </div>

</div>
</body>
</html>
```